Business Card Design For Marketing Agnecy LVP

Need business card design for marketing agency.

Doug Fenwick
President, CEO
1-555-302-4196
doug@boldpromoperksgroup.example
www.BoldPromoPerksGroup.example

Back Side:
Boost Sales Using Rewards, Incentives & Giveaways
Get A Free Sample Package

Target Market(s)

B2B

Industry/Entity Type

Marketing

Contact Information for Business Card

Doug Fenwick
President, CEO
1-555-302-4196

Back Side:
Get A Free Sample Package

Please note that my current url is OLD DESIGN. I am working on new design and want the business card to match color themes at least on new site. Here is the demo link for new site so you can see the colors I use, etc.

http://layoutcratehub.example/kq/doug/lvp_final/index.html

Requirements
Must have
• Please note that my current url is OLD DESIGN. I am working on new design and want the business card to match color themes at least on new site. Here is the demo link for new site so you can see the colors I use, etc.

Nice to have

Should not have

```html
<!DOCTYPE html>
<html lang="en">
<head>
<meta charset="utf-8">
<title>LVP Business Card</title>
<link rel="stylesheet" href="https://fonts.googleapis.com/css2?family=Montserrat:wght@400;700;800&family=Roboto:wght@400&display=swap">
<style>
  :root {
    --stage: #3a3a3c;
    --card-black: #1b1c1e;
    --card-black-2: #232427;
    --brand-blue: #2f64a8;
    --band-gray: #55575b;
    --mark-gray: #6d6f73;
    --white: #ffffff;
  }
  * { margin: 0; padding: 0; box-sizing: border-box; }
  html, body { width: 799px; height: 1200px; overflow: hidden; }
  body {
    background: var(--stage);
    font-family: "Montserrat", sans-serif;
    position: relative;
  }
  .card {
    position: absolute;
    left: 90px;
    width: 620px;
    height: 354px;
    border-radius: 4px;
    overflow: hidden;
    box-shadow: 0 14px 30px rgba(0,0,0,0.45);
  }
  .card--front { top: 120px; background: var(--card-black); }
  .card--back { top: 720px; background: var(--card-black-2); }

  .front-name {
    position: absolute;
    inset: 0;
    display: flex;
    flex-direction: column;
    align-items: center;
    justify-content: center;
    color: var(--mark-gray);
    font-family: "Montserrat", sans-serif;
    font-weight: 800;
    text-transform: uppercase;
  }
  .front-name__short {
    font-size: 116px;
    line-height: 1;
    letter-spacing: 2px;
  }
  .front-name__full {
    margin-top: 14px;
    font-size: 24px;
    letter-spacing: 2px;
  }

  .back-shape { position: absolute; inset: 0; }

  .back-name {
    position: absolute;
    left: 52px; top: 130px;
    font-family: "Montserrat", sans-serif;
    font-weight: 800;
    font-size: 72px;
    color: var(--brand-blue);
    letter-spacing: 1px;
  }

  .back-info {
    position: absolute;
    left: 300px; top: 48px; right: 20px;
    color: var(--white);
  }
  .company {
    font-family: "Montserrat", sans-serif;
    font-weight: 800;
    font-size: 25px;
    line-height: 1.15;
    letter-spacing: 1px;
    text-transform: uppercase;
  }
  .person { margin-top: 32px; }
  .person__name { font-weight: 700; font-size: 22px; }
  .person__title { font-family: "Roboto", sans-serif; font-size: 14px; margin-top: 2px; }
  .contacts { list-style: none; margin-top: 20px; font-family: "Roboto", sans-serif; font-size: 14px; }
  .contacts li { display: flex; align-items: center; gap: 10px; margin-bottom: 6px; }
  .contacts svg { width: 14px; height: 14px; flex: none; }
</style>
</head>
<body>

<section class="card card--front" aria-label="Card front">
  <div class="front-name">
    <span class="front-name__short">LVP</span>
    <span class="front-name__full">Bold Promo Perks Group</span>
  </div>
</section>

<section class="card card--back" aria-label="Card back">
  <svg class="back-shape" viewBox="0 0 620 354" preserveAspectRatio="none">
    <path d="M272 0 Q300 200 170 354 L620 354 L620 0 Z" fill="var(--band-gray)"/>
    <path d="M282 0 Q312 200 190 354 L620 354 L620 0 Z" fill="var(--brand-blue)"/>
  </svg>

  <div class="back-name">LVP</div>

  <div class="back-info">
    <div class="company">Bold Promo<br>Perks Group</div>
    <div class="person">
      <div class="person__name">Doug Fenwick</div>
      <div class="person__title">President, CEO</div>
    </div>
    <ul class="contacts">
      <li>
        <svg viewBox="0 0 24 24" fill="var(--white)"><path d="M6.6 10.8a15 15 0 0 0 6.6 6.6l2.2-2.2a1 1 0 0 1 1-.25 11.4 11.4 0 0 0 3.6.57 1 1 0 0 1 1 1V20a1 1 0 0 1-1 1A17 17 0 0 1 3 4a1 1 0 0 1 1-1h3.5a1 1 0 0 1 1 1c0 1.25.2 2.45.57 3.57a1 1 0 0 1-.25 1z"/></svg>
        1-555-302-4196
      </li>
      <li>
        <svg viewBox="0 0 24 24" fill="var(--white)"><path d="M2 5h20v14H2z M3 6l9 7 9-7" stroke="var(--brand-blue)" stroke-width="1.5"/></svg>
        doug@boldpromoperksgroup.example
      </li>
      <li>
        <svg viewBox="0 0 24 24" fill="none" stroke="var(--white)" stroke-width="2"><circle cx="12" cy="12" r="9"/><path d="M3 12h18M12 3c3 3 3 15 0 18M12 3c-3 3-3 15 0 18"/></svg>
        www.BoldPromoPerksGroup.example
      </li>
    </ul>
  </div>
</section>

</body>
</html>
```